eCommerce website for a DIY shop & communal center

We need a website for a business called The Maple Bench. The Maple Bench is both a shop and communal establishment where people with shared interests, especially in DIY (Do It Yourself) and crafting, can gather to shop for & work on projects while sharing ideas, equipment, supplies and knowledge. The shop is both brick & motor and online. The physical communal space provides workstations, equipment, tools and supplies and expertise for DIY lovers to create their projects.

Target Market(s)

Middle & upper class DIY enthusiasts, creative hobbyists, budding artists & small business owners

Industry/Entity Type

DIY, Arts & Crafts

Coding

Coded - Design and coding required

Number of Pages Required

5+ page

Requirements
Must have
• Menus to include 1. home page (with about us, operating hours, contacts, location, meet the team); 2. Bench activities (how to DIY at the Bench, booking, equipment & tools, house rules); 3. Bench events (events in the Bench, offsite events); 4. Resources (FAQs, tutorials, blogs, eBooks) and 5. Online shop
Nice to have
• Branding guidelines eg logo colours (see attachment) to influence design. Tillpost shop. Booking feature for activities & events at the Bench.

```html
<!DOCTYPE html>
<html lang="en">
<head>
<meta charset="utf-8">
<title>The Maple Bench</title>
<link href="https://fonts.googleapis.com/css2?family=Poppins:wght@300;400;500;600&family=Playfair+Display:ital,wght@1,400;1,500&display=swap" rel="stylesheet">
<style>
:root{
  --pink:#d6126f;
  --ink:#1d1d1d;
  --text:#333;
  --muted:#666;
  --light:#f2f2f2;
  --band:#e9e9e9;
  --white:#fff;
}
*{box-sizing:border-box;margin:0;padding:0}
html,body{width:1200px;height:3808px;overflow:hidden}
body{font-family:'Poppins',sans-serif;color:var(--text);background:var(--white);position:relative}
.abs{position:absolute}
.serif{font-family:'Playfair Display',serif;font-style:italic;font-weight:400}
.pink{color:var(--pink)}

.topnav{left:0;top:0;width:1200px;height:80px;background:var(--light);display:flex;justify-content:center;align-items:center;gap:52px;font-size:19px;color:var(--ink)}
.brand{left:0;top:100px;width:1200px;text-align:center;font-size:46px;font-weight:500;color:var(--ink)}

.hero-photo{left:240px;top:180px;width:960px;height:708px;background:linear-gradient(135deg,#5a4a3c 0%,#c9b8a3 35%,#e8e1d8 55%,#b23a2a 80%,#2a2522 100%)}
.hero-box{left:72px;top:288px;width:448px;height:512px;background:var(--ink);padding:90px 34px 0}
.hero-box h1{color:var(--white);font-size:50px;line-height:1.05}
.hero-box p{color:var(--white);font-size:19px;line-height:1.45;margin-top:18px;font-style:italic;font-weight:300}
.btn{display:inline-block;font-size:17px;color:var(--white);padding:14px 38px}
.btn-pink{background:var(--pink);margin-top:34px}
.btn-dark{background:var(--ink)}

.about-photo{left:72px;top:980px;width:528px;height:500px;border-radius:50%;background:radial-gradient(circle at 45% 40%,#d9c5b5,#8d7a6e 60%,#4f4640)}
.section-h{font-size:58px;font-weight:500;color:var(--ink);line-height:1.05}
.about-h{left:612px;top:1000px}
.copy{font-size:17px;line-height:1.72;color:var(--text)}
.about-copy{left:612px;top:1130px;width:540px}
.about-btn{left:612px;top:1400px}

.act-h{left:0;top:1610px;width:1200px;text-align:center}
.card{top:1732px;width:336px;height:420px;border:3px solid var(--ink);padding:10px}
.card .fill{width:100%;height:100%;display:flex;align-items:center;justify-content:center;text-align:center;border:2px solid var(--white);color:var(--white);font-size:38px;line-height:1.25;padding:20px}
.c1{left:72px}.c1 .fill{background:linear-gradient(160deg,#8b7b74,#4e4440)}
.c2{left:432px}.c2 .fill{background:linear-gradient(160deg,#b59b5e,#5a4c3a)}
.c3{left:792px}.c3 .fill{background:linear-gradient(160deg,#6b5148,#3a2c28)}

.team-band{left:0;top:2240px;width:1200px;height:500px;background:var(--band)}
.team-photo{left:0;top:2240px;width:600px;height:500px;background:linear-gradient(120deg,#c24a3a,#e6c14f 45%,#4a63a8 80%,#2d3450)}
.team-h{left:612px;top:2330px}
.team-copy{left:612px;top:2410px;width:540px}
.team-btn{left:612px;top:2572px}

.book-h{left:72px;top:2800px}
.field{height:62px;border:1px solid #bbb;font-size:15px;color:var(--muted);padding:20px 14px}
.f1{left:72px;top:2948px;width:250px}
.f2{left:338px;top:3028px;width:250px;display:flex;justify-content:space-between}
.f3{left:338px;top:2948px;width:250px}
.f4{left:72px;top:3028px;width:250px}
.f5{left:72px;top:3108px;width:516px;height:120px}
.submit{left:72px;top:3240px;width:220px;height:62px;background:var(--ink);color:var(--white);font-size:17px;display:flex;align-items:center;justify-content:center}

.events-h{left:612px;top:2800px}
.event{left:612px;width:560px;height:124px}
.event .thumb{position:absolute;left:0;top:0;width:180px;height:124px}
.event h3{position:absolute;left:200px;top:0;font-size:26px;color:var(--pink)}
.event p{position:absolute;left:200px;top:42px;width:360px;font-size:15px;line-height:1.6}
.e1{top:2888px}.e1 .thumb{background:linear-gradient(135deg,#c27b5e,#6e4a3a)}
.e2{top:3036px}.e2 .thumb{background:linear-gradient(135deg,#d9832f,#7b3e2a)}
.e3{top:3178px}.e3 .thumb{background:linear-gradient(135deg,#b7a08a,#5c4c40)}

.footer{left:0;top:3400px;width:1200px;height:408px;background:var(--light)}
.foot-col{top:3460px;font-size:15px;line-height:1.5;color:var(--text)}
.foot-col h4{font-size:17px;font-weight:600;color:var(--ink);letter-spacing:.5px;margin-bottom:26px}
.foot-col li{list-style:none;margin-bottom:13px}
.fc1{left:72px}.fc2{left:344px;width:240px}.fc3{left:612px;width:240px}.fc4{left:880px;width:250px}
.hours{display:grid;grid-template-columns:100px 1fr;row-gap:13px}
.closed{color:var(--pink)}
.email-box{border:1px solid #bbb;background:var(--white);height:56px;padding:18px 14px;font-size:14px;color:var(--muted)}
.sub-btn{background:var(--pink);color:var(--white);height:56px;display:flex;align-items:center;justify-content:center;font-size:16px;margin-top:10px}
.copyright{left:72px;top:3752px;font-size:13px;color:var(--text)}
.socials{left:920px;top:3748px;display:flex;gap:20px}
.socials span{width:20px;height:20px;border-radius:50%;background:#444;display:block}
</style>
</head>
<body>

<nav class="abs topnav">
  <span>Home</span><span>Bench Activities</span><span>Bench Events</span><span>Resources</span><span>Online Shop</span>
</nav>

<div class="abs brand">The Maple Bench</div>

<div class="abs hero-photo" role="img" aria-label="Hands painting a colourful geometric pattern on a white sneaker beside paint pots"></div>
<div class="abs hero-box">
  <h1 class="serif">Welcome to<br>The Maple Bench</h1>
  <p>Sed ut perspiciatis unde omnis iste natus error sit voluptatem accusantium</p>
  <span class="btn btn-pink">Read More</span>
</div>

<div class="abs about-photo" role="img" aria-label="Smiling crafter working at a table with paints"></div>
<h2 class="abs section-h about-h">About<br>The Maple <span class="pink">Bench</span></h2>
<p class="abs copy about-copy">Sed ut perspiciatis unde omnis iste natus error sit voluptatem accusantium doloremque laudantium, totam rem aperiam, eaque ipsa quae ab illo inventore veritatis et quasi architecto beatae vitae dicta sunt explicabo. Nemo enim ipsam voluptatem quia voluptas sit aspernatur aut odit aut fugit, sed quia consequuntur magni dolores eos qui ratione voluptatem sequi nesciunt.</p>
<span class="abs btn btn-dark about-btn">Read More</span>

<h2 class="abs section-h act-h">Bench <span class="pink">Activities</span></h2>
<div class="abs card c1"><div class="fill serif" role="img" aria-label="Hands crafting at a workbench">How to DIY at the Bench</div></div>
<div class="abs card c2"><div class="fill serif" role="img" aria-label="Person measuring with tools">Booking, Equipment &amp; Tools</div></div>
<div class="abs card c3"><div class="fill serif" role="img" aria-label="Person reading at the workspace">House Rules</div></div>

<div class="abs team-band"></div>
<div class="abs team-photo" role="img" aria-label="Cheerful group of team members together"></div>
<h2 class="abs section-h team-h">Meet the <span class="pink">Team</span></h2>
<p class="abs copy team-copy">Sed ut perspiciatis unde omnis iste natus error sit voluptatem accusantium doloremque laudantium, totam rem aperiam, eaque ipsa quae ab illo inventore veritatis et quasi architecto beatae vitae dicta sunt explicabo.</p>
<span class="abs btn btn-dark team-btn">Read More</span>

<h2 class="abs section-h book-h">Book Your<br><span class="pink">Activities</span></h2>
<div class="abs field f1">Name</div>
<div class="abs field f3">Email Address</div>
<div class="abs field f4">Phone No</div>
<div class="abs field f2"><span>Select Activity</span>
  <svg width="12" height="10" viewBox="0 0 12 10" style="margin-top:4px"><path d="M1 1 L6 8 L11 1 Z" fill="#333"/></svg></div>
<div class="abs field f5">Message</div>
<div class="abs submit">Submit</div>

<h2 class="abs section-h events-h">Bench <span class="pink">Events</span></h2>
<div class="abs event e1"><div class="thumb" role="img" aria-label="Craft workshop table"></div>
  <h3 class="serif">Sed ut perspiciatis unde</h3><p>Omnis iste natus error sit voluptatem accusantium doloremque laudantium, totam rem aperiam.</p></div>
<div class="abs event e2"><div class="thumb" role="img" aria-label="Child painting with bright colours"></div>
  <h3 class="serif">Sed ut perspiciatis unde</h3><p>Omnis iste natus error sit voluptatem accusantium doloremque laudantium, totam rem aperiam.</p></div>
<div class="abs event e3"><div class="thumb" role="img" aria-label="Hands working on a craft project"></div>
  <h3 class="serif">Sed ut perspiciatis unde</h3><p>Omnis iste natus error sit voluptatem accusantium doloremque laudantium, totam rem aperiam.</p></div>

<footer class="abs footer"></footer>
<div class="abs foot-col fc1"><h4>SITE MAP</h4>
  <ul><li>Home</li><li>Bench Activities</li><li>Bench Events</li><li>Resources</li><li>Online Shop</li></ul></div>
<div class="abs foot-col fc2"><h4>CONTACT US</h4>
  <ul><li>Excepteur sint occaecat<br>cupidatat non</li><li>1-800-555-0142</li><li>hello@maplebench.com</li></ul></div>
<div class="abs foot-col fc3"><h4>HOURS</h4>
  <div class="hours"><span>Mon - Fri</span><span>10am - 8pm</span><span>Sat</span><span>10am - 6pm</span><span>Sunday</span><span class="closed">Closed</span></div></div>
<div class="abs foot-col fc4"><h4>EMAIL SUBSCRIBE</h4>
  <div class="email-box">Email Address</div><div class="sub-btn">Subscribe</div></div>
<div class="abs copyright">Copyright © 2020, The Maple Bench All Right Reserved</div>
<div class="abs socials" aria-label="Social links"><span></span><span></span><span></span><span></span><span></span></div>

</body>
</html>
```